Website for Swedish wellness company "Heartmeadow"

We need a website for our Swedish wellness company. The name is "Heartmeadow" . The company is all about sustainablility for our body, soul and planet. We work with coaching, yoga, massage, healthy food, retreats(sports, excercise, sufing), healing and inspirational talks. We are convinced that personal sustainability and a strong spiritual connection to yourself will lead to planetary sustainability. Our customers are both companies and consumers from all over the world. The final design should be clean/simple and you should get a feeling of community, happiness, warmth, connection,, joy, spirituality but still a professional touch.Just got a logo from Pixel Harbor and are very happy with it;-)
Updates

Sorry I was too enthusiastic posting this project. Of course I will give you some text as well för the different pages! I will see to that it is finished by friday so if you want to wait with your submissions please do! Best regards Maria

Target Market(s)

Businesses and consumers

Industry/Entity Type

Health And Wellness

Number of Pages Required

5+ page

Font styles to use
Sans Serif

Colors
33a6d7
00a990
b7a5cd

Requirements
Must have
• Idea about pages:
• I am not sure how many pages I get for the price, but 5 would be nice to start with.
• Not sure what write ups is;-)
• But title of the pages could be:
• Landing page
• About us
• Services
• Retreats
• Contact us
Nice to have
• A clean and professional website but with some heart and soul in it. Because we Would love colours that harmonize with our logo, but other ideas are welcome!

```html
<!DOCTYPE html>
<html lang="en">
<head>
<meta charset="utf-8">
<title>Heartmeadow</title>
<link rel="stylesheet" href="https://fonts.googleapis.com/css2?family=Marcellus&family=Montserrat:wght@400;500;600&display=swap">
<style>
:root{
  --ink:#1b1b1b;
  --navy:#0f2b63;
  --navy-deep:#0a2050;
  --teal:#5bc4c2;
  --teal-deep:#2f8fa6;
  --text:#555;
  --white:#fff;
  --star:#f2c200;
}
*{margin:0;padding:0;box-sizing:border-box}
html,body{width:1200px;height:3089px;overflow:hidden;background:var(--white)}
body{position:relative;font-family:'Montserrat',sans-serif;color:var(--text)}
.abs{position:absolute}
.serif{font-family:'Marcellus',serif}

/* header */
.hero{left:0;top:98px;width:1200px;height:810px;background:linear-gradient(160deg,#e9e0cf 0%,#f2d6a8 35%,#e7b88a 60%,#b98a6a 80%,#8a6a58 100%)}
.topbar{left:0;top:0;width:1200px;height:98px;background:var(--white)}
.brand-badge{left:46px;top:-90px;width:282px;height:284px;border-radius:50%;background:var(--white)}
.brand-dot{left:167px;top:20px;width:40px;height:40px;border-radius:50%;background:var(--teal)}
.brand-name{left:60px;top:106px;width:254px;text-align:center;font-size:24px;color:var(--navy);font-family:'Marcellus',serif;letter-spacing:1px}
.nav{top:36px;font-family:'Marcellus',serif;font-size:19px;color:var(--ink)}

.hero-title{left:90px;top:368px;font-size:84px;color:var(--ink);letter-spacing:0;line-height:1}
.hero-sub{left:93px;top:476px;font-size:25px;color:var(--navy)}
.btn-join{left:94px;top:578px;width:232px;height:64px;border-radius:32px;background:var(--teal);color:var(--white);font-weight:600;font-size:20px;display:flex;align-items:center;justify-content:center}

/* welcome */
.section-title{width:1200px;left:0;text-align:center;font-family:'Marcellus',serif;color:var(--ink);font-size:46px}
.title-rule{left:576px;width:48px;height:2px;background:#1f3f7a}
.welcome-text{left:110px;width:980px;top:1090px;text-align:center;font-size:15.5px;line-height:30px;color:var(--text)}
.service{top:1228px;width:200px;text-align:center}
.service .art{width:130px;height:136px;margin:0 auto;border-radius:26px}
.service .label{margin-top:30px;font-size:19px;color:#333}
.arrow{width:24px;height:24px}

/* why */
.why-photo{left:0;top:1495px;width:1200px;height:665px;background:linear-gradient(90deg,#4f6f78 0%,#466f7c 30%,#3b7f92 50%,#2e8fa5 65%,#45b0b9 85%,#5cc7c3 100%)}
.why-title{left:650px;top:1632px;font-size:46px;color:var(--white)}
.why-text{left:658px;top:1710px;width:475px;font-size:15.5px;line-height:33px;color:var(--white)}
.btn-read{left:659px;top:1953px;width:174px;height:50px;border:1.5px solid var(--white);border-radius:25px;color:var(--white);font-size:17px;font-weight:500;display:flex;align-items:center;justify-content:center}

/* customers */
.stars{left:540px;top:2318px;width:120px;color:var(--star);font-size:19px;letter-spacing:5px;text-align:center}
.quote{left:120px;width:960px;top:2357px;text-align:center;font-size:15.5px;line-height:26px;color:#444}
.avatar{border-radius:50%}
.person{left:500px;width:200px;text-align:center;top:2558px;font-size:17px;font-weight:600;color:var(--ink)}
.person small{display:block;font-size:12px;font-weight:400;color:#555;margin-top:4px}

/* footer */
.footer{left:0;top:2650px;width:1200px;height:439px;background:linear-gradient(180deg,var(--navy) 0%,var(--navy-deep) 100%)}
.foot-head{top:2808px;font-size:14.5px;color:var(--white);letter-spacing:.3px}
.foot-list{top:2850px;font-size:12px;line-height:25px;color:#dfe6f4}
.foot-list.links span{display:block;text-decoration:underline}
.foot-list.plain span{display:block}
.divider{top:2800px;width:1px;height:160px;background:rgba(255,255,255,.18)}
.contact-row{font-size:12px;color:#dfe6f4;line-height:21px}
.rule{left:90px;top:3008px;width:1020px;height:1px;background:rgba(255,255,255,.2)}
.copy{left:91px;top:3040px;font-size:12px;color:var(--white)}
.follow{left:831px;top:3042px;font-size:11.5px;color:var(--white)}
.social{top:3028px;width:32px;height:32px;border-radius:50%;border:1.5px solid rgba(255,255,255,.8)}
</style>
</head>
<body>

<!-- hero -->
<div class="abs hero" role="img" aria-label="Photo of a woman in child's pose on a yoga mat at a lakeside jetty at sunrise"></div>
<div class="abs topbar"></div>
<div class="abs brand-badge"></div>
<div class="abs brand-dot"></div>
<div class="abs brand-name">HEARTMEADOW</div>
<div class="abs nav" style="left:557px">Home</div>
<div class="abs nav" style="left:656px">About us</div>
<div class="abs nav" style="left:779px">Services</div>
<div class="abs nav" style="left:899px">Retreats</div>
<div class="abs nav" style="left:1018px">Contact us</div>

<div class="abs hero-title serif">HEARTMEADOW</div>
<div class="abs hero-sub">sustainablility for our body, soul and planet</div>
<div class="abs btn-join">Join Us</div>

<svg class="abs" style="left:0;top:800px" width="1200" height="120" viewBox="0 0 1200 120">
  <path d="M0 108 Q600 -5 1200 108 L1200 120 L0 120 Z" fill="#fff"/>
  <circle cx="600" cy="42" r="37" fill="#fff"/>
  <circle cx="600" cy="42" r="19" fill="none" stroke="#1b1b1b" stroke-width="1.6"/>
  <path d="M592 39 L600 47 L608 39" fill="none" stroke="#1b1b1b" stroke-width="1.6"/>
</svg>

<!-- welcome -->
<div class="abs section-title" style="top:978px">Welcome To Heartmeadow</div>
<div class="abs title-rule" style="top:1054px"></div>
<div class="abs welcome-text">Lorem ipsum dolor sit amet, consectetur adipiscing elit, sed do eiusmod tempor incididunt ut labore et dolore magna aliqua. Ut enim ad minim veniam, quis nostrud exercitation ullamco laboris nisi ut aliquip ex ea commodo consequat. Duis aute irure dolor in reprehenderit in voluptate velit esse cillum dolore eu fugiat nulla pariatur.</div>

<svg class="abs arrow" style="left:28px;top:1298px" viewBox="0 0 24 24"><path d="M15 5 L8 12 L15 19" fill="none" stroke="#555" stroke-width="3"/></svg>
<svg class="abs arrow" style="left:1143px;top:1298px" viewBox="0 0 24 24"><path d="M9 5 L16 12 L9 19" fill="none" stroke="#555" stroke-width="3"/></svg>

<div class="abs service" style="left:56px"><div class="art" style="background:#55c2bd" role="img" aria-label="Illustration of a person meditating"></div><div class="label">Yoga</div></div>
<div class="abs service" style="left:279px"><div class="art" style="background:#f8c66a" role="img" aria-label="Illustration of a massage"></div><div class="label">Massage</div></div>
<div class="abs service" style="left:502px"><div class="art" style="background:#5a86e0" role="img" aria-label="Illustration of an apple with fork and knife"></div><div class="label">Healthy Food</div></div>
<div class="abs service" style="left:725px"><div class="art" style="background:#f29ae6" role="img" aria-label="Illustration of people exercising together"></div><div class="label">Retreats</div></div>
<div class="abs service" style="left:948px"><div class="art" style="background:#fde886" role="img" aria-label="Illustration of a healing herb bowl"></div><div class="label">Healing</div></div>

<!-- why choose us -->
<div class="abs why-photo" role="img" aria-label="Photo of a group meditating cross-legged on yoga mats, blending into a teal gradient"></div>
<svg class="abs" style="left:0;top:1490px" width="1200" height="80" viewBox="0 0 1200 80">
  <path d="M0 0 L1200 0 L1200 5 Q600 140 0 5 Z" fill="#fff"/>
</svg>
<svg class="abs" style="left:0;top:2085px" width="1200" height="80" viewBox="0 0 1200 80">
  <path d="M0 70 Q600 -55 1200 70 L1200 80 L0 80 Z" fill="#fff"/>
</svg>
<div class="abs why-title serif">Why Choose Us</div>
<div class="abs why-text">Lorem ipsum dolor sit amet, consectetur adipiscing elit, sed do eiusmod tempor incididunt ut labore et dolore magna aliqua. Ut enim ad minim veniam, quis nostrudtion ullamco laboris nisi ut aliquip ex ea commodo consequat. Duis aute irure dolor in reprehenderit in voluptate velit esse cillum dolore eu fugiat nulla pariatur.</div>
<div class="abs btn-read">Read More</div>

<!-- happy customers -->
<div class="abs section-title" style="top:2222px">Happy Customers</div>
<div class="abs title-rule" style="top:2291px"></div>
<div class="abs stars">★★★★★</div>
<div class="abs quote">Sed ut perspiciatis unde omnis iste natus error sit voluptatem accusantium doloremque laudantium, totam rem aperiam, eaque ipsa quae ab illo inventore veritatis et quasi architecto beatae vitae dicta sunt explicabo</div>
<svg class="abs arrow" style="left:32px;top:2372px" viewBox="0 0 24 24"><path d="M15 5 L8 12 L15 19" fill="none" stroke="#222" stroke-width="3"/></svg>
<svg class="abs arrow" style="left:1144px;top:2372px" viewBox="0 0 24 24"><path d="M9 5 L16 12 L9 19" fill="none" stroke="#222" stroke-width="3"/></svg>
<div class="abs avatar" style="left:399px;top:2436px;width:94px;height:94px;background:#5fb4b3" role="img" aria-label="Customer portrait"></div>
<div class="abs avatar" style="left:542px;top:2428px;width:111px;height:111px;background:#8a6a5e" role="img" aria-label="Portrait of Lena Holm"></div>
<div class="abs avatar" style="left:702px;top:2436px;width:94px;height:94px;background:#5fb4b3" role="img" aria-label="Customer portrait"></div>
<div class="abs person">-Lena Holm<small>City Name</small></div>

<!-- footer -->
<div class="abs footer" role="img" aria-label="Faint navy-tinted photo of a meditating figure behind the footer"></div>
<svg class="abs" style="left:0;top:2640px" width="1200" height="80" viewBox="0 0 1200 80">
  <path d="M0 0 L1200 0 L1200 8 Q600 120 0 8 Z" fill="#fff"/>
</svg>

<div class="abs foot-head" style="left:94px">GET IN TOUCH</div>
<div class="abs foot-list plain" style="left:91px;width:225px;font-size:11px;line-height:23px">At vero eos et accusamus et iusto odio dignissimos ducimus qui blanditiis pra esentium voluptatum delen</div>
<div class="abs divider" style="left:333px"></div>

<div class="abs foot-head" style="left:363px">QUICK LINKS</div>
<div class="abs foot-list links" style="left:364px"><span>Home</span><span>About us</span><span>Services</span><span>Retreats</span><span>Contact us</span></div>
<div class="abs divider" style="left:492px"></div>

<div class="abs foot-head" style="left:514px">PROVIDES</div>
<div class="abs foot-list plain" style="left:515px;line-height:23.5px"><span>Coaching</span><span>Yoga</span><span>Massage</span><span>Healthy food</span><span>Retreats</span></div>
<div class="abs divider" style="left:659px"></div>

<div class="abs foot-head" style="left:700px">LEGAL</div>
<div class="abs foot-list plain" style="left:701px;line-height:26px"><span>Terms &amp; Services</span><span>Privacy policy</span><span>Faq</span><span>Sitemap</span></div>
<div class="abs divider" style="left:862px"></div>

<div class="abs foot-head" style="left:906px">CONTACT US</div>
<svg class="abs" style="left:905px;top:2855px" width="12" height="14" viewBox="0 0 12 14"><path d="M6 0 A5 5 0 0 1 11 5 C11 9 6 14 6 14 C6 14 1 9 1 5 A5 5 0 0 1 6 0 Z" fill="#fff"/><circle cx="6" cy="5" r="2" fill="#0f2b63"/></svg>
<div class="abs contact-row" style="left:936px;top:2852px">Sample Meadow Road 12,<br>Lakeside, 123 45</div>
<svg class="abs" style="left:906px;top:2919px" width="12" height="12" viewBox="0 0 12 12"><path d="M2 0 L4.5 0 L5.5 3 L4 4.5 C4.8 6.2 5.8 7.2 7.5 8 L9 6.5 L12 7.5 L12 10 C12 11 11 12 10 12 C4.5 12 0 7.5 0 2 C0 1 1 0 2 0 Z" fill="#fff"/></svg>
<div class="abs contact-row" style="left:933px;top:2914px">1.555.010.2030</div>
<svg class="abs" style="left:906px;top:2964px" width="13" height="10" viewBox="0 0 13 10"><rect width="13" height="10" rx="1" fill="#fff"/><path d="M0.5 1 L6.5 5.5 L12.5 1" fill="none" stroke="#0f2b63" stroke-width="1.2"/></svg>
<div class="abs contact-row" style="left:938px;top:2958px;text-decoration:underline">hello@heartmeadow.se</div>

<div class="abs rule"></div>
<div class="abs copy">Copyrights © 2019,The Company Name. All Rights Reserved</div>
<div class="abs follow">Follow us on :</div>
<div class="abs social" style="left:922px"></div>
<div class="abs social" style="left:961px"></div>
<div class="abs social" style="left:1000px"></div>
<div class="abs social" style="left:1039px"></div>
<div class="abs social" style="left:1078px"></div>

</body>
</html>
```